Electrictrian Contractor Website Design

We are working with an electrical contractor in California called Fennick Electric.

Some sites to use for content/competitors and inspiration:
https://corvanelectric.example
https://tralvenpage.example/web/contractor/ (lots of contractor website designs we've approved and continue to show clients)

Thank you for taking the time to consider designing a website for us. We are web developers based in Stockton, CA, USA. Most of our projects go through the same process. Understanding this process may help you win a project with us. We custom-code all of our websites in-house. We don’t have any requirements as to what tools you use for your design, but we prefer Figma files. For any design that we label as four-stars, we send it to the client for review. The client picks the final design they want us to use. Once we complete this process, we will continue to show additional clients all the four-star sites and purchase them later. Your designs will have multiple chances to sell. For better chances of success, we ask that you follow these guidelines.

IMAGES:
If you use any images or icons in the design, we ask that you have a link to the asset so we can purchase the image/icon. Most of the designs we submit do not have the customer’s images on them unless they have some great images. Be creative; show us the feeling you are trying to portray with your image choices. Use any royalty-free site you choose. We subscribe to Quorvane and mainly use their images, but we can purchase images outside of Quorvane.

PLEASE NOTE: we will not submit designs to clients with watermarks on the images.

FONTS:
We ask that you identify the fonts used in the design. This can be done in a message if you want. We typically use Pellmarsh Type and Quorvane Type.

CONTENT:
We're always open to different content and ideas. We often submit designs with stock images so the client can see our vision. We typically take pictures after the website launch to use their images with our vision. Lorem Ipsum is fine for paragraphs, but we ask that you write the headers in correct English. We want to be able to show the vision and identify the sections of the website.

INSPIRATION:
We typically add a couple of links in the brief of websites we like to help you get started in your design.

REVISIONS:
We do not often ask for revisions of the designs unless we see something in the design that may not appeal to the client. If there are slight changes that we want to make, we do that in the development process.

FEEDBACK:
We rarely give feedback on designs during the design process. We are working on many website projects and do not have the time to provide feedback. We usually respond if your request is well thought out and asks specific questions, but a note asking “feedback, please” usually goes unanswered

```html
<!DOCTYPE html>
<html lang="en">
<head>
<meta charset="utf-8">
<title>Fennick Electric</title>
<link href="https://fonts.googleapis.com/css2?family=Lato:wght@400;700;900&display=swap" rel="stylesheet">
<style>
:root{
  --blue:#0b3a8a;
  --blue-deep:#082e70;
  --yellow:#f5b301;
  --pale:#fdf0cc;
  --ink:#111111;
  --muted:#6b6b6b;
  --dark:#161212;
  --white:#ffffff;
}
*{margin:0;padding:0;box-sizing:border-box}
html,body{width:1200px;height:3587px;overflow:hidden;background:var(--white)}
body{font-family:'Lato',sans-serif;color:var(--ink)}
.page{position:relative;width:1200px;height:3587px;overflow:hidden}
.abs{position:absolute}
.backdrop{position:absolute;left:0;top:0}
.center{text-align:center}

/* header */
.brand{position:absolute;font-family:'Lato',sans-serif;font-weight:900;color:var(--blue);letter-spacing:6px;line-height:1.05}
.brand-top{left:111px;top:30px;font-size:30px;width:210px;text-align:center}
.brand-top small{display:block;font-size:30px;letter-spacing:8px}
.nav a{position:absolute;top:65px;font-size:16px;color:var(--ink);text-decoration:none;transform:translateX(-50%);white-space:nowrap}
.nav a.active{color:var(--blue);font-weight:700}
.nav-dot{position:absolute;left:416px;top:39px;width:14px;height:14px;border-radius:50%;border:2px solid var(--yellow)}
.call-box{position:absolute;left:944px;top:0;width:256px;height:130px;background:var(--yellow)}
.phone-badge{position:absolute;border-radius:50%;background:var(--blue);display:flex;align-items:center;justify-content:center}
.call-label{position:absolute;font-size:14px;color:var(--blue)}
.call-number{position:absolute;font-size:24px;font-weight:900;color:var(--blue);white-space:nowrap}

/* hero */
.hero-kicker{left:111px;top:222px;font-size:40px;font-weight:900;color:var(--yellow)}
.hero-title{left:108px;top:272px;font-size:64px;font-weight:900;color:var(--white);letter-spacing:-1px}
.hero-text{left:111px;top:358px;width:520px;font-size:18px;font-weight:700;line-height:34px;color:var(--white)}
.btn{position:absolute;display:flex;align-items:center;justify-content:center;background:var(--yellow);border-radius:24px;font-size:16px;font-weight:700;color:var(--blue);text-decoration:none}
.hero-call-label{left:330px;top:448px;font-size:12px;color:var(--white)}
.hero-call-number{left:330px;top:467px;font-size:19px;font-weight:900;color:var(--white)}
.hero-badge{left:568px;top:622px;width:64px;height:64px;border-radius:50%;background:var(--white);box-shadow:0 3px 10px rgba(0,0,0,.15);display:flex;align-items:center;justify-content:center}
.hero-badge span{width:36px;height:36px;border-radius:50%;background:var(--yellow)}

/* common */
.dot{position:absolute;border-radius:50%}
.section-title{position:absolute;left:0;width:1200px;text-align:center;font-size:45px;font-weight:900;letter-spacing:-.5px}
.section-sub{position:absolute;left:0;width:1200px;text-align:center;font-size:18px}
.para{position:absolute;font-size:15px;line-height:28px;color:var(--muted);text-align:center}

/* about */
.photo{position:absolute;overflow:hidden}
.frame{position:absolute;border:1.5px solid var(--yellow)}

/* why */
.why-card{position:absolute;width:439px;height:114px;border-radius:57px;background:var(--white);box-shadow:0 4px 14px rgba(0,0,0,.2)}
.why-icon{position:absolute;left:26px;top:29px;width:56px;height:56px}
.why-card h3{position:absolute;left:122px;top:20px;font-size:20px;font-weight:900;color:var(--blue)}
.why-card p{position:absolute;left:122px;top:50px;width:290px;font-size:14px;line-height:24px;color:var(--muted)}

/* services */
.service-label{position:absolute;width:300px;text-align:center;font-size:22px;font-weight:900;transform:translateX(-50%)}

/* footer */
.brand-foot{left:400px;top:3322px;width:400px;text-align:center;color:var(--white);font-size:46px;letter-spacing:12px}
.brand-foot small{display:block;font-size:46px;letter-spacing:12px}
.foot-nav a,.foot-nav span{position:absolute;top:3442px;font-size:18px;color:var(--white);text-decoration:none;transform:translateX(-50%);white-space:nowrap}
.social{position:absolute;top:3495px;width:34px;height:34px;border-radius:50%;background:var(--blue);transform:translateX(-50%)}
.copyright{left:0;top:3551px;width:1200px;text-align:center;font-size:13px;color:var(--white)}
</style>
</head>
<body>
<div class="page">

<!-- hero imagery -->
<svg class="backdrop" width="1200" height="800" viewBox="0 0 1200 800" role="img" aria-label="Photo of high-voltage transmission towers against a sunset sky">
  <defs>
    <linearGradient id="heroSky" x1="0" y1="0" x2="1" y2="1">
      <stop offset="0" stop-color="#1c2431"/>
      <stop offset=".45" stop-color="#31507e"/>
      <stop offset=".75" stop-color="#6f8fb4"/>
      <stop offset="1" stop-color="#e5b64a"/>
    </linearGradient>
    <linearGradient id="heroShade" x1="0" y1="0" x2="1" y2="0">
      <stop offset="0" stop-color="#0f1520" stop-opacity=".7"/>
      <stop offset=".55" stop-color="#0f1520" stop-opacity=".1"/>
      <stop offset="1" stop-color="#0f1520" stop-opacity="0"/>
    </linearGradient>
  </defs>
  <path d="M0 130 H1200 V536 Q600 764 0 536 Z" fill="url(#heroSky)"/>
  <path d="M0 130 H1200 V536 Q600 764 0 536 Z" fill="url(#heroShade)"/>
</svg>

<!-- shapes -->
<svg class="backdrop" width="1200" height="3587" viewBox="0 0 1200 3587" aria-hidden="true" style="pointer-events:none">
  <path d="M104 571 Q600 765 1093 571 Q600 741 104 571 Z" fill="var(--blue)"/>
  <rect x="0" y="1286" width="1200" height="820" fill="var(--blue)"/>
  <circle cx="600" cy="1666" r="170" fill="var(--yellow)"/>
  <path d="M111 2015 Q600 1821 1089 2015 Q600 1849 111 2015 Z" fill="var(--yellow)"/>
  <path d="M0 2060 Q600 1810 1200 2060 V2120 H0 Z" fill="var(--white)"/>
  <rect x="0" y="3104" width="1200" height="483" fill="var(--dark)"/>
  <path d="M104 3148 Q600 3365 1096 3148 Q600 3340 104 3148 Z" fill="var(--yellow)"/>
  <path d="M0 3104 Q600 3382 1200 3104 Z" fill="var(--white)"/>
</svg>

<!-- header -->
<div class="brand brand-top">FENNICK<small>ELECTRIC</small></div>
<nav class="nav">
  <span class="nav-dot"></span>
  <a class="active" href="#">Home</a>
  <a href="#" style="left:539px">About Us</a>
  <a href="#" style="left:663px">Services</a>
  <a href="#" style="left:813px">Why Choose Us?</a>
</nav>
<style>.nav a.active{left:423px}</style>
<div class="call-box"></div>
<div class="phone-badge" style="left:918px;top:39px;width:50px;height:50px">
  <svg width="20" height="20" viewBox="0 0 24 24"><path d="M6.6 10.8a15 15 0 0 0 6.6 6.6l2.2-2.2a1 1 0 0 1 1-.25 11.4 11.4 0 0 0 3.6.6 1 1 0 0 1 1 1V20a1 1 0 0 1-1 1A17 17 0 0 1 3 4a1 1 0 0 1 1-1h3.5a1 1 0 0 1 1 1c0 1.25.2 2.45.6 3.6a1 1 0 0 1-.25 1z" fill="#fff"/></svg>
</div>
<div class="call-label" style="left:995px;top:41px">Call Us:</div>
<div class="call-number" style="left:995px;top:61px">+1 555 010 4418</div>

<!-- hero -->
<div class="abs hero-kicker">WELCOME TO</div>
<h1 class="abs hero-title">FENNICK ELECTRIC</h1>
<p class="abs hero-text">Lorem ipsum dolor sit amet, consectetur adipiscing elit, sed do eiusmod tempor incididunt ut labore et dolo</p>
<a class="btn" href="#" style="left:111px;top:448px;width:142px;height:42px">Get Started</a>
<div class="phone-badge" style="left:273px;top:448px;width:42px;height:42px">
  <svg width="16" height="16" viewBox="0 0 24 24"><path d="M6.6 10.8a15 15 0 0 0 6.6 6.6l2.2-2.2a1 1 0 0 1 1-.25 11.4 11.4 0 0 0 3.6.6 1 1 0 0 1 1 1V20a1 1 0 0 1-1 1A17 17 0 0 1 3 4a1 1 0 0 1 1-1h3.5a1 1 0 0 1 1 1c0 1.25.2 2.45.6 3.6a1 1 0 0 1-.25 1z" fill="var(--yellow)"/></svg>
</div>
<div class="abs hero-call-label">Call Us:</div>
<div class="abs hero-call-number">+1 555 010 4418</div>
<div class="abs hero-badge"><span></span></div>

<div class="dot" style="left:55px;top:637px;width:70px;height:70px;background:var(--pale)"></div>
<div class="dot" style="left:1137px;top:647px;width:126px;height:126px;background:var(--yellow)"></div>

<!-- about -->
<div class="frame" style="left:113px;top:779px;width:240px;height:348px;border-radius:120px 0 120px 120px"></div>
<div class="photo" role="img" aria-label="Photo of a lit transmission tower under a starry night sky" style="left:125px;top:791px;width:240px;height:348px;border-radius:120px 0 120px 120px;background:linear-gradient(160deg,#1d3c73 0%,#2d5b93 45%,#c97a2a 75%,#0f1626 100%)"></div>
<div class="frame" style="left:399px;top:835px;width:240px;height:347px;border-radius:120px 120px 120px 0"></div>
<div class="photo" role="img" aria-label="Photo of an electrician installing a ceiling light while homeowners watch" style="left:388px;top:824px;width:238px;height:345px;border-radius:119px 119px 119px 0;background:linear-gradient(170deg,#e8e6e2 0%,#cfccc6 50%,#8d8b86 100%)"></div>

<h2 class="section-title" style="left:741px;width:300px;top:814px">ABOUT US</h2>
<p class="para" style="left:690px;top:886px;width:402px">Sed ut perspiciatis unde omnis iste natus error sit voluptatem accusantium doloremque laudantium, totam rem aperiam, eaque ipsa quae ab illo inventore veritatis et quasi architecto beatae vitae</p>
<p class="para" style="left:690px;top:1013px;width:402px">Nemo enim ipsam voluptatem quia voluptas sit aspernatur aut odit aut fugit, sed quia</p>
<a class="btn" href="#" style="left:820px;top:1093px;width:142px;height:41px">Read More</a>

<!-- why choose us -->
<h2 class="section-title" style="top:1355px;color:var(--white)">WHY CHOOSE US</h2>
<p class="section-sub" style="top:1420px;color:var(--white)">Sed ut perspiciatis unde omnis iste natus error sit voluptatem accusantium doloremque</p>

<div class="why-card" style="left:111px;top:1513px">
  <svg class="why-icon" viewBox="0 0 56 56" aria-hidden="true"><circle cx="28" cy="28" r="25" fill="none" stroke="var(--blue)" stroke-width="2.5"/><circle cx="28" cy="28" r="8" fill="var(--yellow)"/></svg>
  <h3>VOLUPTATEM ACCUSANT</h3>
  <p>Sed ut perspiciatis unde omnis iste natus err or sit voluptatem accusantium dolor</p>
</div>
<div class="why-card" style="left:650px;top:1513px">
  <svg class="why-icon" viewBox="0 0 56 56" aria-hidden="true"><circle cx="28" cy="28" r="25" fill="none" stroke="var(--blue)" stroke-width="2.5"/><circle cx="28" cy="28" r="8" fill="var(--yellow)"/></svg>
  <h3>VOLUPTATEM ACCUSANT</h3>
  <p>Sed ut perspiciatis unde omnis iste natus err or sit voluptatem accusantium dolor</p>
</div>
<div class="why-card" style="left:111px;top:1684px">
  <svg class="why-icon" viewBox="0 0 56 56" aria-hidden="true"><circle cx="28" cy="28" r="25" fill="none" stroke="var(--blue)" stroke-width="2.5"/><circle cx="28" cy="28" r="8" fill="var(--yellow)"/></svg>
  <h3>VOLUPTATEM ACCUSANT</h3>
  <p>Sed ut perspiciatis unde omnis iste natus err or sit voluptatem accusantium dolor</p>
</div>
<div class="why-card" style="left:650px;top:1684px">
  <svg class="why-icon" viewBox="0 0 56 56" aria-hidden="true"><circle cx="28" cy="28" r="25" fill="none" stroke="var(--blue)" stroke-width="2.5"/><circle cx="28" cy="28" r="8" fill="var(--yellow)"/></svg>
  <h3>VOLUPTATEM ACCUSANT</h3>
  <p>Sed ut perspiciatis unde omnis iste natus err or sit voluptatem accusantium dolor</p>
</div>

<!-- services -->
<h2 class="section-title" style="top:2030px">OUR SERVICES</h2>
<p class="section-sub" style="top:2097px;color:var(--muted)">Sed ut perspiciatis unde omnis iste natus error sit voluptatem accusantium doloremque</p>

<svg class="backdrop" width="1200" height="2500" viewBox="0 0 1200 2500" aria-hidden="true" style="pointer-events:none">
  <circle cx="262" cy="2311" r="142" fill="none" stroke="var(--yellow)" stroke-width="16" stroke-dasharray="720 172" transform="rotate(-60 262 2311)"/>
  <circle cx="600" cy="2311" r="142" fill="none" stroke="var(--blue)" stroke-width="16" stroke-dasharray="720 172" transform="rotate(-60 600 2311)"/>
  <circle cx="938" cy="2311" r="142" fill="none" stroke="var(--yellow)" stroke-width="16" stroke-dasharray="720 172" transform="rotate(-60 938 2311)"/>
</svg>
<div class="photo" role="img" aria-label="Photo of two line workers beneath a transmission tower at night" style="left:130px;top:2179px;width:264px;height:264px;border-radius:50%;background:linear-gradient(170deg,#1f3f78,#4d6fa3 60%,#2a2a30)"></div>
<div class="photo" role="img" aria-label="Photo of a technician silhouetted beneath a steel pylon at dusk" style="left:468px;top:2179px;width:264px;height:264px;border-radius:50%;background:linear-gradient(170deg,#4f78b0,#9db5cf 55%,#d98a3a 80%,#1a1a1a)"></div>
<div class="photo" role="img" aria-label="Photo of an engineer in a hard hat working on a laptop at a substation" style="left:806px;top:2179px;width:264px;height:264px;border-radius:50%;background:linear-gradient(170deg,#5a5f7a,#8a6e78 50%,#c0603a 80%,#2a2220)"></div>
<div class="service-label" style="left:262px;top:2490px">INSTALL</div>
<div class="service-label" style="left:600px;top:2490px">MAINTENANCE</div>
<div class="service-label" style="left:938px;top:2490px">24/7 SUPPORT</div>

<!-- questions -->
<div class="dot" style="left:79px;top:2585px;width:48px;height:48px;background:var(--pale)"></div>
<h2 class="section-title" style="left:87px;width:500px;top:2662px;line-height:57px">GOT QUESTIONS?<br>WE'VE GOT ANSWERS</h2>
<p class="para" style="left:136px;top:2794px;width:402px">Sed ut perspiciatis unde omnis iste natus error sit voluptatem accusantium doloremque laudantium, totam rem aperiam, eaque ipsa quae ab illo inventore veritatis et quasi architecto beatae vitae</p>
<p class="para" style="left:136px;top:2926px;width:402px">Nemo enim ipsam voluptatem quia voluptas sit aspernatur aut odit aut fugit, sed quia</p>
<a class="btn" href="#" style="left:267px;top:3007px;width:142px;height:42px">Read More</a>
<div class="photo" role="img" aria-label="Photo of a smiling electrician shaking hands with a homeowner in a kitchen" style="left:608px;top:2636px;width:481px;height:452px;border-radius:90px 90px 90px 90px;background:linear-gradient(160deg,#dfe3e6 0%,#c5ccd2 45%,#8e97a0 100%)"></div>
<div class="dot" style="left:1104px;top:3037px;width:70px;height:70px;background:var(--pale)"></div>

<!-- footer -->
<div class="brand brand-foot">FENNICK<small>ELECTRIC</small></div>
<nav class="foot-nav">
  <a href="#" style="left:228px">Home</a>
  <span style="left:301px">|</span>
  <a href="#" style="left:386px">About Us</a>
  <span style="left:470px">|</span>
  <a href="#" style="left:550px">Services</a>
  <span style="left:632px">|</span>
  <a href="#" style="left:745px">Why Choose Us?</a>
  <span style="left:859px">|</span>
  <a href="#" style="left:951px">Contact Us</a>
</nav>
<span class="social" style="left:555px"></span>
<span class="social" style="left:600px"></span>
<span class="social" style="left:643px"></span>
<div class="abs copyright">(C) Copyright 2024 | All Rights Reserved</div>

</div>
</body>
</html>
```